Brightfen Business Card Redesign & Logo Update

We need to update our business cards to something more modern and fresh. Brightfen can provide the current color schemes and old design examples, but welcome creativity in helping us with this redesign. PLEASE NOTE that we no longer utilize the "tree" and/or "leaf" imagery in our branding. If able would apprecaite an update on the quality of our "words only" logo in Ai. / PNG formats too.

Target Market(s)

Investors, landowners, corporate partners, contractors

Industry/Entity Type

Environmental Restoration & Conservation

Contact Information for Business Card

Logo, persons name, title, mailing address, phone and email, website url

Font styles to use
Other font styles liked:
• Merriweather

Requirements
Nice to have
• Logo, persons name, title, mailing address, phone and email, website url, but open to ideams
Should not have
• No all back backgrounds

```html
<!DOCTYPE html>
<html lang="en">
<head>
<meta charset="utf-8">
<title>Brightfen Business Card</title>
<link rel="stylesheet" href="https://fonts.googleapis.com/css2?family=Merriweather:wght@400;700;900&family=Oswald:wght@600&display=swap">
<style>
  :root {
    --backdrop: #e6e6e6;
    --card: #ffffff;
    --green: #177c3f;
    --orange: #ee8021;
    --ink: #1b1b1b;
  }
  * { margin: 0; padding: 0; box-sizing: border-box; }
  html, body { width: 1146px; height: 1200px; overflow: hidden; }
  body { background: var(--backdrop); position: relative; font-family: "Merriweather", Georgia, serif; color: var(--ink); }

  .card { position: absolute; left: 176px; width: 797px; background: var(--card); overflow: hidden; }
  .card--front { top: 115px; height: 453px; }
  .card--back { top: 596px; height: 466px; }

  .wordmark { font-family: "Merriweather", Georgia, serif; font-weight: 900; color: var(--green); letter-spacing: 2px; white-space: nowrap; }
  .tagline { font-family: "Oswald", "Arial Narrow", sans-serif; font-weight: 600; color: var(--ink); text-transform: uppercase; white-space: nowrap; }

  .front-brand { position: absolute; left: 0; right: 0; top: 168px; text-align: center; }
  .front-brand .wordmark { font-size: 68px; line-height: 1; }
  .front-brand .tagline { font-size: 22px; margin-top: 14px; letter-spacing: 0.3px; }

  .person { position: absolute; left: 0; top: 89px; padding-left: 30px; }
  .person__marker { position: absolute; left: 0; top: 0; width: 12px; height: 51px; background: var(--orange); }
  .person__name { font-size: 26px; font-weight: 700; line-height: 1.1; letter-spacing: 0.3px; }
  .person__first { color: var(--orange); }
  .person__last { color: var(--green); }
  .person__title { font-size: 21px; margin-top: 6px; }

  .address { position: absolute; left: 30px; top: 173px; font-size: 21px; line-height: 29px; }
  .contacts { position: absolute; left: 30px; top: 257px; list-style: none; font-size: 21px; line-height: 28px; }
  .contacts li { display: flex; align-items: center; gap: 8px; }
  .contacts svg { width: 15px; height: 15px; flex: none; }

  .divider { position: absolute; left: 390px; top: 91px; width: 2px; height: 249px; background: var(--orange); }

  .back-brand { position: absolute; left: 392px; right: 0; top: 180px; text-align: center; }
  .back-brand .wordmark { font-size: 46px; line-height: 1; letter-spacing: 1px; }
  .back-brand .tagline { font-size: 15.5px; margin-top: 10px; }

  .wave { position: absolute; left: 0; top: 0; width: 797px; height: 466px; }
</style>
</head>
<body>
  <section class="card card--front">
    <div class="front-brand">
      <div class="wordmark">BRIGHTFEN</div>
      <div class="tagline">Environmental Credit Company</div>
    </div>
  </section>

  <section class="card card--back">
    <svg class="wave" viewBox="0 0 797 466" aria-hidden="true">
      <path d="M0 368 C 180 395 340 440 500 428 C 620 418 720 398 797 404 L797 466 L0 466 Z" fill="var(--green)"/>
      <path d="M42 378 C 220 402 400 420 560 400 C 650 389 720 392 770 404 C 720 398 650 396 560 410 C 400 432 220 416 42 378 Z" fill="var(--orange)"/>
    </svg>

    <div class="person">
      <span class="person__marker"></span>
      <div class="person__name"><span class="person__first">NOLAN</span> <span class="person__last">REYES</span></div>
      <div class="person__title">Founder</div>
    </div>

    <address class="address" style="font-style:normal">
      Your Company Address<br>
      Fen Rd. 48, PO 2210, BF
    </address>

    <ul class="contacts">
      <li>
        <svg viewBox="0 0 16 16" aria-hidden="true"><path d="M3 2h3l1.5 3.5-2 1.2a8 8 0 0 0 3.8 3.8l1.2-2L14 10v3a1.5 1.5 0 0 1-1.5 1.5A11 11 0 0 1 1.5 3.5 1.5 1.5 0 0 1 3 2z" fill="var(--orange)"/></svg>
        (555) 014-2290
      </li>
      <li>
        <svg viewBox="0 0 16 16" aria-hidden="true"><rect x="1" y="3.5" width="14" height="9.5" rx="1" fill="var(--orange)"/><path d="M1.5 4.2 8 9l6.5-4.8" stroke="#fff" stroke-width="1.3" fill="none"/></svg>
        hello@brightfenmail.com
      </li>
      <li>
        <svg viewBox="0 0 16 16" aria-hidden="true"><circle cx="8" cy="8" r="7" fill="var(--orange)"/><path d="M1 8h14M8 1c-3 3.5-3 10.5 0 14M8 1c3 3.5 3 10.5 0 14" stroke="#fff" stroke-width="1.1" fill="none"/></svg>
        www.brightfen.com
      </li>
    </ul>

    <span class="divider"></span>

    <div class="back-brand">
      <div class="wordmark">BRIGHTFEN</div>
      <div class="tagline">Environmental Credit Company</div>
    </div>
  </section>
</body>
</html>
```